Business Card Design Project

We are a construction company in Orange County, CA. We need a two sided business card. We would like the back to be our logo with web URL. Front should included Name, title, address, phone, fax and email address.

our address is
627 West Dorrance Blvd, Suite 308
Anaheim, CA 92718

Our logo files are attached.

Construction

```html
<!DOCTYPE html>
<html lang="en">
<head>
<meta charset="utf-8">
<title>Halvern Business Card</title>
<link rel="stylesheet" href="https://fonts.googleapis.com/css2?family=Open+Sans:wght@400;600;700;800&display=swap">
<style>
  :root {
    --brand-blue: #1a4b7e;
    --ink: #3a3a3a;
    --ink-soft: #4a4a4a;
    --card-white: #ffffff;
    --card-edge: #c9c9c9;
    --backdrop: #e6e2dc;
    --divider: #8a8a8a;
  }
  * { box-sizing: border-box; margin: 0; padding: 0; }
  html, body {
    width: 1200px;
    height: 402px;
    overflow: hidden;
    background: var(--backdrop);
    font-family: "Open Sans", Arial, sans-serif;
  }
  .canvas {
    position: relative;
    width: 1200px;
    height: 402px;
  }
  .card {
    position: absolute;
    top: 60px;
    width: 512px;
    height: 291px;
  }
  .card-front {
    left: 73px;
    background: var(--card-white);
    border: 1px solid var(--card-edge);
    text-align: center;
    color: var(--ink);
  }
  .card-back {
    left: 637px;
    background: var(--brand-blue);
    display: flex;
    align-items: center;
    justify-content: center;
  }
  .wordmark {
    font-weight: 800;
    letter-spacing: 1px;
    line-height: 1;
  }
  .card-front .wordmark {
    margin-top: 30px;
    font-size: 72px;
    color: var(--brand-blue);
  }
  .card-back .wordmark {
    font-size: 82px;
    color: var(--card-white);
  }
  .holder {
    margin-top: 56px;
    font-size: 15px;
    color: var(--ink);
  }
  .holder-name { font-weight: 700; }
  .contacts {
    margin-top: 22px;
    display: flex;
    justify-content: center;
    gap: 10px;
    font-size: 13px;
    color: var(--ink-soft);
  }
  .contact-col { display: flex; flex-direction: column; gap: 2px; }
  .contact-col.numbers { align-items: flex-end; }
  .contact-col.online { align-items: flex-start; }
  .contact-rule {
    width: 1px;
    background: var(--divider);
  }
  .contact-line {
    display: flex;
    align-items: center;
    gap: 5px;
    line-height: 18px;
  }
  .contact-line svg { width: 10px; height: 10px; fill: var(--ink-soft); }
  .address {
    margin-top: 10px;
    font-size: 13px;
    color: var(--ink-soft);
  }
</style>
</head>
<body>
<main class="canvas">
  <section class="card card-front" aria-label="Card front">
    <div class="wordmark">HALVERN</div>
    <p class="holder"><span class="holder-name">Your Name,</span> Title</p>
    <div class="contacts">
      <div class="contact-col numbers">
        <div class="contact-line">
          <svg viewBox="0 0 10 10" aria-hidden="true"><path d="M2 0.5 L3.6 2.6 L2.7 3.6 Q3.8 6 6.4 7.3 L7.4 6.4 L9.5 8 L8.3 9.5 Q2.5 8.5 0.5 1.7 Z"/></svg>
          <span>01-234-5678</span>
        </div>
        <div class="contact-line">
          <svg viewBox="0 0 10 10" aria-hidden="true"><rect x="2.5" y="0.5" width="5" height="3"/><rect x="0.5" y="3.5" width="9" height="4" rx="1"/><rect x="2.5" y="6.5" width="5" height="3"/></svg>
          <span>01-234-5678</span>
        </div>
      </div>
      <div class="contact-rule"></div>
      <div class="contact-col online">
        <div class="contact-line">
          <svg viewBox="0 0 10 10" aria-hidden="true"><path d="M0.5 2 H9.5 V8 H0.5 Z M0.5 2 L5 5.5 L9.5 2" fill="none" stroke="#4a4a4a" stroke-width="1"/><path d="M0.5 2 L5 5.3 L9.5 2 V8 H0.5 Z"/></svg>
          <span>info@halvernbuild.com</span>
        </div>
        <div class="contact-line">
          <svg viewBox="0 0 10 10" aria-hidden="true"><circle cx="5" cy="5" r="4.5"/><path d="M0.5 5 H9.5 M5 0.5 Q2.5 5 5 9.5 M5 0.5 Q7.5 5 5 9.5" fill="none" stroke="#fff" stroke-width="0.7"/></svg>
          <span>www.halvernbuild.com</span>
        </div>
      </div>
    </div>
    <p class="address">627 West Dorrance Blvd, Suite 308, Anaheim, CA&nbsp; 92718</p>
  </section>

  <section class="card card-back" aria-label="Card back">
    <div class="wordmark">HALVERN</div>
  </section>
</main>
</body>
</html>
```